Banner Ad Designs for tick and flea products

We sell tick and flea products online and want some great banner designs for our online website to promote our tick and flea products.

The ads must be made up in both Flash and HTML5
Ads can be formatted as .JPEG or .GIF files.

Please see the following url for creative requirements
http://help.bannerkite.com/creative-requirements/

Creative licence no limits to your imagination!

Ads must be created in the following sizes:

- Banner – 468×60
- Square – 250×250
- Small Square – 200×200
- Leaderboard – 728×90
- Medium Rectangle – 300×250
- Chatterly – 100×72

please view our website at www.globalpawstore.com.au or .com to get a feel for our website.

The aim is to attract customers who want to save on tick and flea purchases for their pets (dogs and cats)

Target Market(s)

Anyone who owns a dog or cat

Industry/Entity Type

Online

Font styles to use
Sans Serif
Other font styles liked:
• creative licence on font styles

Requirements
Must have
• Must have a strong urge to entice customers to click through.

Images wording and text etc use creative lic
Nice to have
• Strong appeal to dog and cat owners and how they can save on flea and tick essentials.
Keep it simple but effective.
Be fun and playful and inviting.
Should not have
• Please do not use words like cheap - cheapest

Strobing & Flashing - Strobing, flashing backgrounds, or otherwise distracting ads are not allowed. Do not attempt to overtly distract the user from page content.

```html
<!DOCTYPE html>
<html lang="en">
<head>
<meta charset="utf-8">
<title>Tick and Flea Banner Set</title>
<link rel="stylesheet" href="https://fonts.googleapis.com/css2?family=Questrial&family=Oswald:wght@500&display=swap">
<style>
  :root {
    --page: #ffffff;
    --stage: #6b6b6b;
    --banner-green: #84ad32;
    --ring-outer: #a9c86a;
    --ring-inner: #c8dc9f;
    --panel: #ffffff;
    --headline: #fbfbef;
    --brand-ink: #1f2a44;
    --label-ink: #111111;
    --button-top: #7fe05a;
    --button-bottom: #1e9a2c;
    --button-edge: #d7f5c4;
    --button-text: #f5f028;
  }
  * { margin: 0; padding: 0; box-sizing: border-box; }
  html, body { width: 1200px; height: 900px; overflow: hidden; background: var(--page); }
  .canvas { position: relative; width: 1200px; height: 900px; background: var(--page); }
  .stage { position: absolute; left: 0; top: 93px; width: 1200px; height: 653px; background: var(--stage); }
  .variant-label {
    position: absolute; left: 10px; width: 40px;
    font-family: "Questrial", sans-serif; font-size: 54px; color: var(--label-ink);
    line-height: 1;
  }
  .banner {
    position: absolute; left: 70px; width: 1091px; height: 134px;
    background: var(--banner-green); overflow: hidden;
  }
  .pet-photo {
    position: absolute; left: 0; top: 0; width: 156px; height: 100%;
    background: linear-gradient(90deg, #e6ded4 0%, #c8ab88 35%, #8f7458 60%, #f4f1ea 85%, var(--banner-green) 100%);
  }
  .pug-photo {
    position: absolute; right: 0; top: 0; width: 156px; height: 100%;
    background: linear-gradient(90deg, var(--banner-green) 0%, #d9c08f 25%, #b8955f 55%, #6c5a3c 80%, #a88c5e 100%);
  }
  .headline {
    position: absolute; font-family: "Questrial", sans-serif; color: var(--headline);
    text-align: center; white-space: nowrap; letter-spacing: 0.5px;
  }
  .headline--two-line { left: 180px; width: 560px; top: 20px; font-size: 42px; line-height: 48px; }
  .headline--wide { left: 290px; width: 500px; top: 36px; font-size: 55px; line-height: 60px; }
  .headline--short { left: 180px; width: 560px; top: 8px; font-size: 47px; line-height: 54px; }
  .brand-panel { position: absolute; right: 0; top: 0; width: 307px; height: 134px; }
  .brand-name {
    position: absolute; right: 0; top: 0; width: 240px; height: 134px;
    display: flex; align-items: center; justify-content: center;
    font-family: "Questrial", sans-serif; font-size: 31px; color: var(--brand-ink);
  }
  .order-button {
    position: absolute; left: 367px; top: 71px; width: 196px; height: 51px;
    border: 2px solid var(--button-edge); border-radius: 6px;
    background: linear-gradient(180deg, var(--button-top), var(--button-bottom));
    font-family: "Oswald", sans-serif; font-size: 27px; color: var(--button-text);
    display: flex; align-items: center; justify-content: center; letter-spacing: 1px;
  }
</style>
</head>
<body>
<div class="canvas">
  <div class="stage"></div>

  <div class="variant-label" style="top:210px">A</div>
  <section class="banner" style="top:186px">
    <div class="pet-photo" role="img" aria-label="Photo of a small dog and a tabby cat lying together"></div>
    <p class="headline headline--two-line">Save on genuine brand<br>tick and flea products</p>
    <div class="brand-panel">
      <svg width="307" height="134" viewBox="0 0 307 134" aria-hidden="true">
        <circle cx="205" cy="67" r="185" fill="var(--ring-outer)"/>
        <circle cx="205" cy="67" r="168" fill="var(--ring-inner)"/>
        <circle cx="205" cy="67" r="152" fill="var(--panel)"/>
      </svg>
      <div class="brand-name">Global Paw Store</div>
    </div>
  </section>

  <div class="variant-label" style="top:382px">B</div>
  <section class="banner" style="top:355px">
    <div class="pet-photo" role="img" aria-label="Photo of a small dog and a tabby cat lying together"></div>
    <p class="headline headline--wide">Protect Your Pets!</p>
    <div class="pug-photo" role="img" aria-label="Photo of three pugs sitting in a row"></div>
  </section>

  <div class="variant-label" style="top:558px">C</div>
  <section class="banner" style="top:532px">
    <div class="pet-photo" role="img" aria-label="Photo of a small dog and a tabby cat lying together"></div>
    <p class="headline headline--short">Save with us</p>
    <a class="order-button">ORDER NOW</a>
    <div class="brand-panel">
      <svg width="307" height="134" viewBox="0 0 307 134" aria-hidden="true">
        <circle cx="205" cy="67" r="185" fill="var(--ring-outer)"/>
        <circle cx="205" cy="67" r="168" fill="var(--ring-inner)"/>
        <circle cx="205" cy="67" r="152" fill="var(--panel)"/>
      </svg>
      <div class="brand-name">Global Paw Store</div>
    </div>
  </section>
</div>
</body>
</html>
```